Restaurant Digital TV Menu Pictures

Need a digital menu board, image square of food. Something simple for customer to look and point to or say the food number. Image square 4x6, 5x7 or various of that. Vietnamese restaurant type food. I need template created and designer choice of design. Color scheme orange and white and little green. I would like to in the title of the food myself and written detail myself. I just need the template and possible have the design edit the picture a bit. Total food about 30 image will mostly be about 20-30 images. This will be display on a TV screen 16:9 size on a 55 inch tv. Attached is the food menu item. Also attach how the image off food will be taken. Also attach of other people design on the web. However, I would like number be label on the food item. I can find tune the correct information and food type and numbers later.

Font styles to use
Decorative

Colors
f37122
fffefb
9bcb3c

Requirements
Must have
• Photo edit food image basic making it pop. Make it look better, not magic, but better than my photography. Asian feel to the design.
Nice to have
• Fresh image of ingredients, (cilantro, freshly cook, non fast food) Image of green food

```html
<!DOCTYPE html>
<html lang="en">
<head>
<meta charset="utf-8">
<title>Lotus Bowl Asian Cuisine – Digital Menu Board</title>
<link href="https://fonts.googleapis.com/css2?family=Bebas+Neue&family=Oswald:wght@500&family=Montserrat:wght@500;800&display=swap" rel="stylesheet">
<style>
  :root {
    --orange: #f37122;
    --orange-light: #f79a4e;
    --cream: #fffefb;
    --green: #9bcb3c;
    --green-dark: #6fa821;
    --board: #1f1f1f;
    --ink: #2a2a2a;
    --stage: #d6d6d6;
  }
  * { box-sizing: border-box; margin: 0; padding: 0; }
  html, body { width: 768px; height: 1200px; overflow: hidden; }
  body { background: var(--stage); position: relative; font-family: "Montserrat", sans-serif; }

  /* 16:9 screen: 728 x 410 */
  .menu-board {
    position: absolute; left: 20px; top: 395px;
    width: 728px; height: 410px;
    background: var(--cream);
    display: flex; flex-direction: column;
  }
  .board-header {
    height: 58px; flex: none;
    display: flex; flex-direction: column;
    align-items: center; justify-content: center; gap: 3px;
  }
  .brand-mark {
    width: 30px; height: 30px; border-radius: 50%;
    border: 2.5px solid var(--orange);
  }
  .brand-name {
    font-family: "Oswald", sans-serif; font-weight: 500;
    font-size: 7px; line-height: 8px; letter-spacing: .4px; color: var(--ink);
  }

  .board-body {
    flex: 1; background: var(--board);
    display: flex; gap: 10px; padding: 11px 10px;
  }
  .menu-grid {
    display: grid;
    grid-template-columns: repeat(5, 115px);
    grid-template-rows: repeat(4, 78px);
    gap: 6px;
  }
  .menu-card {
    border: 2px solid var(--orange);
    background: var(--cream);
    display: flex; flex-direction: column;
    overflow: hidden;
  }
  .card-title {
    position: relative;
    height: 13px; flex: none;
    background: linear-gradient(var(--orange-light), var(--orange));
    color: var(--cream);
    font-family: "Bebas Neue", sans-serif; font-weight: 400;
    font-size: 11px; line-height: 13px; letter-spacing: .5px;
    text-align: center;
  }
  .item-number {
    position: absolute; left: 2px; top: 1.5px;
    width: 10px; height: 10px; border-radius: 50%;
    background: var(--green-dark); color: var(--cream);
    font-family: "Oswald", sans-serif; font-weight: 500;
    font-size: 6.5px; line-height: 10px; letter-spacing: 0;
    text-align: center;
  }
  .card-content { position: relative; flex: 1; }
  .card-desc {
    position: absolute; left: 4px; top: 3px; width: 44px;
    font-size: 3.2px; line-height: 4.2px; color: var(--ink);
  }
  .card-photo {
    position: absolute; right: 3px; top: 3px;
    width: 54px; height: 54px; border-radius: 50%;
    border: 1.5px solid var(--orange);
    box-shadow: 0 0 0 1.2px var(--green);
  }
  .photo-beef { background: radial-gradient(circle at 55% 55%, #6b4632 0 30%, #3a2a22 45%, #141414 70%); }
  .photo-popcorn { background: radial-gradient(circle at 55% 55%, #c97a32 0 30%, #e3a458 50%, #f6f1ea 70%); }
  .card-price {
    position: absolute; left: 4px; bottom: 10px;
    font-family: "Oswald", sans-serif; font-weight: 500;
    font-size: 11px; line-height: 12px; color: var(--orange);
  }
  .order-bar {
    position: absolute; left: 0; bottom: 1px;
    width: 52px; height: 8px;
    background: linear-gradient(90deg, var(--green-dark), var(--green));
    clip-path: polygon(0 0, 100% 0, 90% 100%, 0 100%);
    display: flex; align-items: center; gap: 2px; padding-left: 2px;
    font-size: 4.5px; line-height: 8px; font-weight: 800; color: #111;
  }
  .order-bar svg { width: 5px; height: 5px; flex: none; }

  .info-board {
    width: 96px; height: 330px;
    background: var(--cream); border: 3px solid var(--orange);
    display: flex; flex-direction: column; align-items: center;
    padding-top: 8px;
    font-family: "Oswald", sans-serif; font-weight: 500; color: var(--ink);
  }
  .info-board .info { font-size: 26px; line-height: 30px; }
  .info-board .board-word {
    font-size: 46px; line-height: 56px;
    display: flex; flex-direction: column; align-items: center;
  }
</style>
</head>
<body>
<main class="menu-board">
  <header class="board-header">
    <span class="brand-mark"></span>
    <span class="brand-name">Lotus Bowl Asian Cuisine</span>
  </header>

  <section class="board-body">
    <div class="menu-grid">
      <article class="menu-card"><h2 class="card-title"><span class="item-number">1</span>BEEF RICE</h2><div class="card-content"><p class="card-desc">Lorem ipsum dolor sit amet, consectetur adipiscing elit, sed do eiusmod tempor incididunt.</p><div class="card-photo photo-beef" role="img" aria-label="Photo of grilled beef rice bowl with slaw and spring roll"></div><p class="card-price">$9.99</p><p class="order-bar"><svg viewBox="0 0 10 10"><circle cx="5" cy="5" r="4.5" fill="#fff"/><path d="M3 5h4M5 3l2 2-2 2" stroke="#111" stroke-width="1.2" fill="none"/></svg>ORDER NOW</p></div></article>
      <article class="menu-card"><h2 class="card-title"><span class="item-number">2</span>POPCORN</h2><div class="card-content"><p class="card-desc">Lorem ipsum dolor sit amet, consectetur adipiscing elit, sed do eiusmod tempor incididunt.</p><div class="card-photo photo-popcorn" role="img" aria-label="Photo of crispy popcorn chicken with cilantro"></div><p class="card-price">$6.99</p><p class="order-bar"><svg viewBox="0 0 10 10"><circle cx="5" cy="5" r="4.5" fill="#fff"/><path d="M3 5h4M5 3l2 2-2 2" stroke="#111" stroke-width="1.2" fill="none"/></svg>ORDER NOW</p></div></article>
      <article class="menu-card"><h2 class="card-title"><span class="item-number">3</span>BEEF RICE</h2><div class="card-content"><p class="card-desc">Lorem ipsum dolor sit amet, consectetur adipiscing elit, sed do eiusmod tempor incididunt.</p><div class="card-photo photo-beef" role="img" aria-label="Photo of grilled beef rice bowl with slaw and spring roll"></div><p class="card-price">$9.99</p><p class="order-bar"><svg viewBox="0 0 10 10"><circle cx="5" cy="5" r="4.5" fill="#fff"/><path d="M3 5h4M5 3l2 2-2 2" stroke="#111" stroke-width="1.2" fill="none"/></svg>ORDER NOW</p></div></article>
      <article class="menu-card"><h2 class="card-title"><span class="item-number">4</span>POPCORN</h2><div class="card-content"><p class="card-desc">Lorem ipsum dolor sit amet, consectetur adipiscing elit, sed do eiusmod tempor incididunt.</p><div class="card-photo photo-popcorn" role="img" aria-label="Photo of crispy popcorn chicken with cilantro"></div><p class="card-price">$6.99</p><p class="order-bar"><svg viewBox="0 0 10 10"><circle cx="5" cy="5" r="4.5" fill="#fff"/><path d="M3 5h4M5 3l2 2-2 2" stroke="#111" stroke-width="1.2" fill="none"/></svg>ORDER NOW</p></div></article>
      <article class="menu-card"><h2 class="card-title"><span class="item-number">5</span>POPCORN</h2><div class="card-content"><p class="card-desc">Lorem ipsum dolor sit amet, consectetur adipiscing elit, sed do eiusmod tempor incididunt.</p><div class="card-photo photo-popcorn" role="img" aria-label="Photo of crispy popcorn chicken with cilantro"></div><p class="card-price">$6.99</p><p class="order-bar"><svg viewBox="0 0 10 10"><circle cx="5" cy="5" r="4.5" fill="#fff"/><path d="M3 5h4M5 3l2 2-2 2" stroke="#111" stroke-width="1.2" fill="none"/></svg>ORDER NOW</p></div></article>

      <article class="menu-card"><h2 class="card-title"><span class="item-number">6</span>BEEF RICE</h2><div class="card-content"><p class="card-desc">Lorem ipsum dolor sit amet, consectetur adipiscing elit, sed do eiusmod tempor incididunt.</p><div class="card-photo photo-beef" role="img" aria-label="Photo of grilled beef rice bowl with slaw and spring roll"></div><p class="card-price">$9.99</p><p class="order-bar"><svg viewBox="0 0 10 10"><circle cx="5" cy="5" r="4.5" fill="#fff"/><path d="M3 5h4M5 3l2 2-2 2" stroke="#111" stroke-width="1.2" fill="none"/></svg>ORDER NOW</p></div></article>
      <article class="menu-card"><h2 class="card-title"><span class="item-number">7</span>POPCORN</h2><div class="card-content"><p class="card-desc">Lorem ipsum dolor sit amet, consectetur adipiscing elit, sed do eiusmod tempor incididunt.</p><div class="card-photo photo-popcorn" role="img" aria-label="Photo of crispy popcorn chicken with cilantro"></div><p class="card-price">$6.99</p><p class="order-bar"><svg viewBox="0 0 10 10"><circle cx="5" cy="5" r="4.5" fill="#fff"/><path d="M3 5h4M5 3l2 2-2 2" stroke="#111" stroke-width="1.2" fill="none"/></svg>ORDER NOW</p></div></article>
      <article class="menu-card"><h2 class="card-title"><span class="item-number">8</span>BEEF RICE</h2><div class="card-content"><p class="card-desc">Lorem ipsum dolor sit amet, consectetur adipiscing elit, sed do eiusmod tempor incididunt.</p><div class="card-photo photo-beef" role="img" aria-label="Photo of grilled beef rice bowl with slaw and spring roll"></div><p class="card-price">$9.99</p><p class="order-bar"><svg viewBox="0 0 10 10"><circle cx="5" cy="5" r="4.5" fill="#fff"/><path d="M3 5h4M5 3l2 2-2 2" stroke="#111" stroke-width="1.2" fill="none"/></svg>ORDER NOW</p></div></article>
      <article class="menu-card"><h2 class="card-title"><span class="item-number">9</span>POPCORN</h2><div class="card-content"><p class="card-desc">Lorem ipsum dolor sit amet, consectetur adipiscing elit, sed do eiusmod tempor incididunt.</p><div class="card-photo photo-popcorn" role="img" aria-label="Photo of crispy popcorn chicken with cilantro"></div><p class="card-price">$6.99</p><p class="order-bar"><svg viewBox="0 0 10 10"><circle cx="5" cy="5" r="4.5" fill="#fff"/><path d="M3 5h4M5 3l2 2-2 2" stroke="#111" stroke-width="1.2" fill="none"/></svg>ORDER NOW</p></div></article>
      <article class="menu-card"><h2 class="card-title"><span class="item-number">10</span>POPCORN</h2><div class="card-content"><p class="card-desc">Lorem ipsum dolor sit amet, consectetur adipiscing elit, sed do eiusmod tempor incididunt.</p><div class="card-photo photo-popcorn" role="img" aria-label="Photo of crispy popcorn chicken with cilantro"></div><p class="card-price">$6.99</p><p class="order-bar"><svg viewBox="0 0 10 10"><circle cx="5" cy="5" r="4.5" fill="#fff"/><path d="M3 5h4M5 3l2 2-2 2" stroke="#111" stroke-width="1.2" fill="none"/></svg>ORDER NOW</p></div></article>

      <article class="menu-card"><h2 class="card-title"><span class="item-number">11</span>BEEF RICE</h2><div class="card-content"><p class="card-desc">Lorem ipsum dolor sit amet, consectetur adipiscing elit, sed do eiusmod tempor incididunt.</p><div class="card-photo photo-beef" role="img" aria-label="Photo of grilled beef rice bowl with slaw and spring roll"></div><p class="card-price">$9.99</p><p class="order-bar"><svg viewBox="0 0 10 10"><circle cx="5" cy="5" r="4.5" fill="#fff"/><path d="M3 5h4M5 3l2 2-2 2" stroke="#111" stroke-width="1.2" fill="none"/></svg>ORDER NOW</p></div></article>
      <article class="menu-card"><h2 class="card-title"><span class="item-number">12</span>POPCORN</h2><div class="card-content"><p class="card-desc">Lorem ipsum dolor sit amet, consectetur adipiscing elit, sed do eiusmod tempor incididunt.</p><div class="card-photo photo-popcorn" role="img" aria-label="Photo of crispy popcorn chicken with cilantro"></div><p class="card-price">$6.99</p><p class="order-bar"><svg viewBox="0 0 10 10"><circle cx="5" cy="5" r="4.5" fill="#fff"/><path d="M3 5h4M5 3l2 2-2 2" stroke="#111" stroke-width="1.2" fill="none"/></svg>ORDER NOW</p></div></article>
      <article class="menu-card"><h2 class="card-title"><span class="item-number">13</span>BEEF RICE</h2><div class="card-content"><p class="card-desc">Lorem ipsum dolor sit amet, consectetur adipiscing elit, sed do eiusmod tempor incididunt.</p><div class="card-photo photo-beef" role="img" aria-label="Photo of grilled beef rice bowl with slaw and spring roll"></div><p class="card-price">$9.99</p><p class="order-bar"><svg viewBox="0 0 10 10"><circle cx="5" cy="5" r="4.5" fill="#fff"/><path d="M3 5h4M5 3l2 2-2 2" stroke="#111" stroke-width="1.2" fill="none"/></svg>ORDER NOW</p></div></article>
      <article class="menu-card"><h2 class="card-title"><span class="item-number">14</span>POPCORN</h2><div class="card-content"><p class="card-desc">Lorem ipsum dolor sit amet, consectetur adipiscing elit, sed do eiusmod tempor incididunt.</p><div class="card-photo photo-popcorn" role="img" aria-label="Photo of crispy popcorn chicken with cilantro"></div><p class="card-price">$6.99</p><p class="order-bar"><svg viewBox="0 0 10 10"><circle cx="5" cy="5" r="4.5" fill="#fff"/><path d="M3 5h4M5 3l2 2-2 2" stroke="#111" stroke-width="1.2" fill="none"/></svg>ORDER NOW</p></div></article>
      <article class="menu-card"><h2 class="card-title"><span class="item-number">15</span>POPCORN</h2><div class="card-content"><p class="card-desc">Lorem ipsum dolor sit amet, consectetur adipiscing elit, sed do eiusmod tempor incididunt.</p><div class="card-photo photo-popcorn" role="img" aria-label="Photo of crispy popcorn chicken with cilantro"></div><p class="card-price">$6.99</p><p class="order-bar"><svg viewBox="0 0 10 10"><circle cx="5" cy="5" r="4.5" fill="#fff"/><path d="M3 5h4M5 3l2 2-2 2" stroke="#111" stroke-width="1.2" fill="none"/></svg>ORDER NOW</p></div></article>

      <article class="menu-card"><h2 class="card-title"><span class="item-number">16</span>BEEF RICE</h2><div class="card-content"><p class="card-desc">Lorem ipsum dolor sit amet, consectetur adipiscing elit, sed do eiusmod tempor incididunt.</p><div class="card-photo photo-beef" role="img" aria-label="Photo of grilled beef rice bowl with slaw and spring roll"></div><p class="card-price">$9.99</p><p class="order-bar"><svg viewBox="0 0 10 10"><circle cx="5" cy="5" r="4.5" fill="#fff"/><path d="M3 5h4M5 3l2 2-2 2" stroke="#111" stroke-width="1.2" fill="none"/></svg>ORDER NOW</p></div></article>
      <article class="menu-card"><h2 class="card-title"><span class="item-number">17</span>POPCORN</h2><div class="card-content"><p class="card-desc">Lorem ipsum dolor sit amet, consectetur adipiscing elit, sed do eiusmod tempor incididunt.</p><div class="card-photo photo-popcorn" role="img" aria-label="Photo of crispy popcorn chicken with cilantro"></div><p class="card-price">$6.99</p><p class="order-bar"><svg viewBox="0 0 10 10"><circle cx="5" cy="5" r="4.5" fill="#fff"/><path d="M3 5h4M5 3l2 2-2 2" stroke="#111" stroke-width="1.2" fill="none"/></svg>ORDER NOW</p></div></article>
      <article class="menu-card"><h2 class="card-title"><span class="item-number">18</span>BEEF RICE</h2><div class="card-content"><p class="card-desc">Lorem ipsum dolor sit amet, consectetur adipiscing elit, sed do eiusmod tempor incididunt.</p><div class="card-photo photo-beef" role="img" aria-label="Photo of grilled beef rice bowl with slaw and spring roll"></div><p class="card-price">$9.99</p><p class="order-bar"><svg viewBox="0 0 10 10"><circle cx="5" cy="5" r="4.5" fill="#fff"/><path d="M3 5h4M5 3l2 2-2 2" stroke="#111" stroke-width="1.2" fill="none"/></svg>ORDER NOW</p></div></article>
      <article class="menu-card"><h2 class="card-title"><span class="item-number">19</span>POPCORN</h2><div class="card-content"><p class="card-desc">Lorem ipsum dolor sit amet, consectetur adipiscing elit, sed do eiusmod tempor incididunt.</p><div class="card-photo photo-popcorn" role="img" aria-label="Photo of crispy popcorn chicken with cilantro"></div><p class="card-price">$6.99</p><p class="order-bar"><svg viewBox="0 0 10 10"><circle cx="5" cy="5" r="4.5" fill="#fff"/><path d="M3 5h4M5 3l2 2-2 2" stroke="#111" stroke-width="1.2" fill="none"/></svg>ORDER NOW</p></div></article>
      <article class="menu-card"><h2 class="card-title"><span class="item-number">20</span>POPCORN</h2><div class="card-content"><p class="card-desc">Lorem ipsum dolor sit amet, consectetur adipiscing elit, sed do eiusmod tempor incididunt.</p><div class="card-photo photo-popcorn" role="img" aria-label="Photo of crispy popcorn chicken with cilantro"></div><p class="card-price">$6.99</p><p class="order-bar"><svg viewBox="0 0 10 10"><circle cx="5" cy="5" r="4.5" fill="#fff"/><path d="M3 5h4M5 3l2 2-2 2" stroke="#111" stroke-width="1.2" fill="none"/></svg>ORDER NOW</p></div></article>
    </div>

    <aside class="info-board">
      <span class="info">INFO</span>
      <span class="board-word"><span>B</span><span>O</span><span>A</span><span>R</span><span>D</span></span>
    </aside>
  </section>
</main>
</body>
</html>
```